New manufacturing IT architecture concept powerpoint presentation

Create an appealing PowerPoint presentation, from handmade sketches, to illustrate a new approach to manufacturing IT architectures. We want to present the idea to augment the experience of people working in manufacturing plants using AI based on the data that our systems normally collect. We even want to present the power of having a tier 2 Manufacturing execution system that can coordinate and optimize production between multiple plants of the same corporate. The target audience is IT managers, Operations Managers, plant managers, engineering managers, and Continuous improvement managers.
Target Market(s)
Manufacturing companies mostly in Food & Bev and CPG. Mostly big multinational companies
Industry/Entity Type
Software manufacturing solutions (MES/MOM)
Font styles to use
Other font styles liked:
- Segoe
Look and feel

```html
<!DOCTYPE html>
<html lang="en">
<head>
<meta charset="utf-8">
<title>KALDENA_OPS – Unified Operation Center deck</title>
<link rel="stylesheet" href="https://fonts.googleapis.com/css2?family=Poppins:wght@400;500;600;700&display=swap">
<style>
:root{
  --page:#eef0f2;
  --blue:#1f6fbf;
  --blue-light:#3fa0de;
  --teal:#3ab5b3;
  --ink:#111418;
  --muted:#3a3f46;
  --sand:#fbeec4;
  --slide:#ffffff;
  --diagram-bg:#f6f8fb;
  --grey-slide:#e6e7e9;
}
*{box-sizing:border-box;margin:0;padding:0}
html,body{width:1200px;height:4057px;overflow:hidden}
body{background:var(--page);font-family:"Poppins",sans-serif;color:var(--ink);position:relative}
.slide{position:absolute;left:66px;width:1066px;height:600px;background:var(--slide);overflow:hidden;box-shadow:0 1px 3px rgba(0,0,0,.08)}
.slide svg.layer{position:absolute;left:0;top:0}
.footer{position:absolute;left:0;bottom:0;width:100%;height:29px;display:flex;font-size:9px;color:#fff;align-items:center}
.footer .copy{background:var(--blue);width:458px;height:100%;display:flex;align-items:center;padding-left:24px}
.footer .tab{background:#fff;width:150px;height:100%;display:flex;align-items:center;justify-content:center;font-weight:700;font-size:18px;color:var(--blue);white-space:nowrap}
.footer .page{background:var(--teal);flex:1;height:100%;display:flex;align-items:center;justify-content:flex-end;padding-right:20px}
.brand{font-weight:700;color:var(--blue);letter-spacing:1px;white-space:nowrap}
.photo{position:absolute}
.cover .brand{position:absolute;left:24px;top:138px;font-size:48px}
.cover h1{position:absolute;left:27px;top:236px;font-size:34px;line-height:43px;font-weight:600;width:460px}
.intro .text{position:absolute;left:570px;top:88px;width:480px}
.intro h2{font-size:23px;line-height:34px;font-weight:600}
.intro p{margin-top:14px;font-size:12.5px;line-height:34.5px;color:var(--muted);white-space:nowrap}
.people{background:var(--diagram-bg)}
.topline{position:absolute;left:0;top:0;width:100%;height:3px;background:var(--blue)}
.node-label{position:absolute;font-size:22px;font-weight:500;color:var(--ink)}
.hub-label{position:absolute;left:432px;top:256px;width:200px;text-align:center;font-size:24px;font-weight:600;color:#fff}
.box{position:absolute;display:flex;flex-direction:column;align-items:center;justify-content:flex-end;padding-bottom:26px;color:#fff;font-weight:600;font-size:19px;text-align:center}
.box svg{margin-bottom:12px}
.box.streams{left:424px;top:22px;width:220px;height:137px;background:var(--blue)}
.box.people-box{left:113px;top:214px;width:361px;height:137px;background:var(--teal)}
.box.corp{left:594px;top:214px;width:360px;height:137px;background:var(--teal)}
.box.aom{left:298px;top:406px;width:471px;height:137px;background:var(--blue-light)}
.pillars .list{position:absolute;left:570px;top:28px;width:470px}
.pillar{margin-bottom:13px}
.pillar h3{font-size:20px;font-weight:600;line-height:28px}
.pillar .sub{font-size:12.5px;color:var(--muted);line-height:20px}
.pillar .point{position:relative;padding-left:23px;font-size:12px;line-height:21.5px;color:var(--muted);margin-top:3px}
.pillar .point::before{content:"";position:absolute;left:1px;top:5px;width:10px;height:10px;border:2px solid var(--blue);border-radius:50%;box-shadow:inset 0 0 0 2px #fff;background:var(--blue)}
.closing{background:var(--grey-slide)}
.closing .brand{position:absolute;left:28px;top:136px;font-size:50px}
.closing h2{position:absolute;left:32px;top:205px;font-size:76px;font-weight:700;letter-spacing:-1px}
.closing .mail{position:absolute;left:40px;top:316px;font-size:22px;display:flex;align-items:center;gap:10px;color:var(--muted)}
</style>
</head>
<body>

<section class="slide cover" style="top:102px">
  <svg class="layer" width="1066" height="600" viewBox="0 0 1066 600">
    <defs>
      <linearGradient id="g-cover" x1="0" y1="0" x2="1" y2="1">
        <stop offset="0" stop-color="#c9d3e6"/><stop offset=".55" stop-color="#4a5f86"/><stop offset="1" stop-color="#16213d"/>
      </linearGradient>
    </defs>
    <polygon points="664,0 1066,0 1066,600 660,600 494,252" fill="url(#g-cover)" role="img" aria-label="Photo: hands of a business person gesturing over a laptop with digital circuit graphics"/>
    <polyline points="493,302 662,420 552,600" fill="none" stroke="#9fd6d3" stroke-width="1.2"/>
    <polygon points="576,600 710,418 1066,600" fill="var(--blue)"/>
  </svg>
  <div class="brand">KALDENA_OPS</div>
  <h1>Unified Operation Center &amp; Augmented Operation Management</h1>
</section>

<section class="slide intro" style="top:754px">
  <div class="photo" style="left:0;top:0;width:532px;height:571px;background:linear-gradient(135deg,#5a4a3c,#a88a6c 45%,#2e2a28)" role="img" aria-label="Photo: team of colleagues gathered around a laptop in an office"></div>
  <div class="text">
    <h2>How digitalization evolved in last years from being technology focused to user and value focused</h2>
    <p>Sed ut perspiciatis unde omnis iste natus error sit voluptatem<br>accusantium doloremque laudantium, totam rem aperiam, eaque<br>ipsa quae ab illo inventore veritatis et quasi architecto beatae vitae<br>dicta sunt explicabo. Nemo enim ipsam voluptatem quia voluptas sit<br>aspernatur aut odit aut fugit, sed quia consequuntur magni dolores<br>eos qui ratione voluptatem sequi nesciunt. Neque porro quisquam<br>est, qui dolorem ipsum quia</p>
  </div>
  <div class="footer"><div class="copy">©Copyright ©2022 KALDENA_OPS. All Rights Reserved.</div><div class="tab">KALDENA_OPS</div><div class="page">PAGE 1</div></div>
</section>

<section class="slide people" style="top:1405px">
  <div class="topline"></div>
  <svg class="layer" width="1066" height="600" viewBox="0 0 1066 600">
    <defs>
      <linearGradient id="g-hub" x1="0" y1="0" x2="0" y2="1">
        <stop offset="0" stop-color="#3ab5b3"/><stop offset="1" stop-color="#1f6fbf"/>
      </linearGradient>
    </defs>
    <path d="M0,10 C120,-10 260,60 420,20 L420,0 L0,0Z M0,10 C40,60 30,150 0,170Z" fill="var(--sand)" opacity=".75"/>
    <path d="M640,600 C700,480 860,540 1066,470 L1066,600Z" fill="var(--sand)" opacity=".75"/>
    <path d="M0,520 C120,470 220,560 340,600 L0,600Z" fill="var(--sand)" opacity=".5"/>
    <g fill="none" stroke="#2a3a4a" stroke-width="1.6">
      <polyline points="540,164 540,80 493,80"/>
      <polyline points="611,189 784,189 784,150"/>
      <polyline points="431,209 387,209 387,282 206,282 206,258"/>
      <polyline points="647,282 678,282 678,223 854,223 854,246"/>
      <polyline points="410,304 340,304 340,343"/>
      <polyline points="611,358 734,358 734,387"/>
      <polyline points="500,391 500,433"/>
    </g>
    <g fill="var(--teal)">
      <circle cx="540" cy="164" r="4"/><circle cx="611" cy="189" r="4"/><circle cx="431" cy="209" r="4"/>
      <circle cx="647" cy="282" r="4"/><circle cx="410" cy="304" r="4"/><circle cx="611" cy="358" r="4"/><circle cx="500" cy="391" r="4"/>
    </g>
    <circle cx="532" cy="274" r="116" fill="#fff" stroke="#b9c2cc" stroke-width="3"/>
    <circle cx="532" cy="274" r="106" fill="url(#g-hub)"/>
    <g>
      <g transform="translate(449,82)"><circle r="44" fill="#fff" stroke="#d5dce4" stroke-width="2"/><circle r="38" fill="var(--blue)"/><rect x="-12" y="-10" width="24" height="16" fill="none" stroke="#fff" stroke-width="2"/><line x1="0" y1="6" x2="0" y2="14" stroke="#fff" stroke-width="2"/></g>
      <g transform="translate(783,109)"><circle r="44" fill="#fff" stroke="#d5dce4" stroke-width="2"/><circle r="38" fill="var(--blue)"/><circle cy="-5" r="9" fill="none" stroke="#fff" stroke-width="2"/><path d="M-14,12 H14" stroke="#fff" stroke-width="2"/></g>
      <g transform="translate(209,219)"><circle r="44" fill="#fff" stroke="#d5dce4" stroke-width="2"/><circle r="38" fill="var(--blue)"/><circle cy="-4" r="11" fill="none" stroke="#fff" stroke-width="2"/><path d="M-5,10 H5 M-4,15 H4" stroke="#fff" stroke-width="2"/></g>
      <g transform="translate(862,287)"><circle r="44" fill="#fff" stroke="#d5dce4" stroke-width="2"/><circle r="38" fill="var(--blue)"/><rect x="-13" y="-6" width="26" height="16" fill="none" stroke="#fff" stroke-width="2"/><rect x="-6" y="-14" width="12" height="8" fill="none" stroke="#fff" stroke-width="2"/></g>
      <g transform="translate(342,387)"><circle r="44" fill="#fff" stroke="#d5dce4" stroke-width="2"/><circle r="38" fill="var(--blue)"/><path d="M-12,-10 L10,-6 L4,12 L-10,8Z M-12,-10 L4,12 M10,-6 L-10,8" fill="none" stroke="#fff" stroke-width="2"/></g>
      <g transform="translate(737,428)"><circle r="44" fill="#fff" stroke="#d5dce4" stroke-width="2"/><circle r="38" fill="var(--blue)"/><path d="M-14,-2 L-4,-10 L6,0 L14,-6 M-14,6 L-4,12 L8,4" fill="none" stroke="#fff" stroke-width="2"/></g>
      <g transform="translate(501,474)"><circle r="44" fill="#fff" stroke="#d5dce4" stroke-width="2"/><circle r="38" fill="var(--blue)"/><circle r="9" fill="none" stroke="#fff" stroke-width="2"/><circle cx="-8" cy="-8" r="5" fill="none" stroke="#fff" stroke-width="2"/><circle cx="9" cy="9" r="5" fill="none" stroke="#fff" stroke-width="2"/></g>
    </g>
  </svg>
  <div class="hub-label">PEOPLE</div>
  <div class="node-label" style="left:331px;top:60px">Train</div>
  <div class="node-label" style="left:649px;top:86px">Inform</div>
  <div class="node-label" style="left:287px;top:195px">Skill</div>
  <div class="node-label" style="left:693px;top:265px">Augment</div>
  <div class="node-label" style="left:186px;top:363px">Connect</div>
  <div class="node-label" style="left:803px;top:408px">Unify</div>
  <div class="node-label" style="left:558px;top:454px">Coordinate</div>
  <div class="footer"><div class="copy">©Copyright ©2022 KALDENA_OPS. All Rights Reserved.</div><div class="tab">KALDENA_OPS</div><div class="page">PAGE 2</div></div>
</section>

<section class="slide people" style="top:2056px">
  <div class="topline"></div>
  <svg class="layer" width="1066" height="600" viewBox="0 0 1066 600">
    <path d="M0,10 C120,-10 260,60 420,20 L420,0 L0,0Z M0,10 C40,60 30,150 0,170Z" fill="var(--sand)" opacity=".75"/>
    <path d="M640,600 C700,480 860,540 1066,470 L1066,600Z" fill="var(--sand)" opacity=".75"/>
    <g fill="none" stroke="#2a3a4a" stroke-width="1.6">
      <polyline points="299,212 299,140 768,140 768,212"/>
      <polyline points="77,284 77,476 296,476"/>
      <polyline points="989,284 989,476 771,476"/>
    </g>
    <g fill="none" stroke="var(--blue)" stroke-width="1.6">
      <path d="M294,178 l5,6 l5,-6 M294,184 l5,6 l5,-6"/>
      <path d="M763,178 l5,6 l5,-6 M763,184 l5,6 l5,-6"/>
      <path d="M72,310 l5,6 l5,-6 M72,316 l5,6 l5,-6"/>
      <path d="M984,310 l5,6 l5,-6 M984,316 l5,6 l5,-6"/>
      <path d="M264,471 l6,5 l-6,5 M270,471 l6,5 l-6,5"/>
      <path d="M800,471 l-6,5 l6,5 M794,471 l-6,5 l6,5"/>
    </g>
    <g fill="var(--teal)"><circle cx="299" cy="140" r="4"/><circle cx="768" cy="140" r="4"/><circle cx="77" cy="284" r="4"/><circle cx="989" cy="284" r="4"/><circle cx="77" cy="476" r="4"/><circle cx="989" cy="476" r="4"/></g>
  </svg>
  <div class="box streams"><svg width="60" height="44" viewBox="0 0 60 44" fill="none" stroke="#fff" stroke-width="2.4"><circle cx="30" cy="22" r="5"/><path d="M20,12a14,14 0 0,0 0,20 M40,12a14,14 0 0,1 0,20 M13,5a24,24 0 0,0 0,34 M47,5a24,24 0 0,1 0,34"/></svg>2 MAIN STREAMS</div>
  <div class="box people-box"><svg width="40" height="52" viewBox="0 0 40 52" fill="none" stroke="#fff" stroke-width="2.2"><circle cx="20" cy="16" r="11"/><path d="M4,50 C4,36 36,36 36,50"/></svg>AUGMENT PEOPLE</div>
  <div class="box corp"><svg width="56" height="52" viewBox="0 0 56 52" fill="none" stroke="#fff" stroke-width="2.2"><rect x="4" y="18" width="14" height="32"/><rect x="20" y="4" width="16" height="46"/><rect x="38" y="14" width="14" height="36"/></svg>AUGMENT CORPORATE VISIBILITY</div>
  <div class="box aom"><svg width="56" height="50" viewBox="0 0 56 50" fill="none" stroke="#fff" stroke-width="2.2"><circle cx="28" cy="16" r="10"/><circle cx="28" cy="16" r="4"/><path d="M6,34 L20,30 L30,38 L50,30 M10,44 L26,44"/></svg>AUGMENTED OPERATIONS MANAGEMENT</div>
  <div class="footer"><div class="copy">©Copyright ©2022 KALDENA_OPS. All Rights Reserved.</div><div class="tab">KALDENA_OPS</div><div class="page">PAGE 3</div></div>
</section>

<section class="slide pillars" style="top:2707px">
  <div class="photo" style="left:0;top:0;width:532px;height:571px;background:linear-gradient(135deg,#3c4656,#c7d0dc 50%,#e9edf2)" role="img" aria-label="Photo: business person at a laptop with network data graphics"></div>
  <div class="list">
    <div class="pillar"><h3>Linked KPIs</h3><div class="sub">Global, Regional, Plant/facility/operations, Equipment</div>
      <div class="point">Operations manager can take decisions with a corporate vision and dispatch them to plants. Any decision become instantly action</div></div>
    <div class="pillar"><h3>Cross functional collaboration</h3>
      <div class="point">Data and information of different departments are correlated and generate an holistic view to take decision in close loop</div></div>
    <div class="pillar"><h3>Supply chain coordination</h3>
      <div class="point">Data coming from different plants/systems are correlated to optimize supply chain decisions with a multi plant approach. Internal supply chain managed as a whole</div></div>
    <div class="pillar"><h3>Production optimization</h3>
      <div class="point">Production optimized at a corporate level and not only at a plant level. Decisions taken at the corporate operations control level</div></div>
    <div class="pillar"><h3>Knowledge capturing and nurturing</h3>
      <div class="point">Knowledge of users collected at corporate level and made available to any user with no geography, time or language limitation. Reduced onboarding, increased efficiency, better engagement</div></div>
  </div>
  <div class="footer"><div class="copy">©Copyright ©2022 KALDENA_OPS. All Rights Reserved.</div><div class="tab">KALDENA_OPS</div><div class="page">PAGE 4</div></div>
</section>

<section class="slide closing" style="top:3358px">
  <svg class="layer" width="1066" height="600" viewBox="0 0 1066 600">
    <defs>
      <linearGradient id="g-close" x1="0" y1="0" x2="1" y2="1">
        <stop offset="0" stop-color="#dfe3e8"/><stop offset=".5" stop-color="#6d7a8c"/><stop offset="1" stop-color="#2b3442"/>
      </linearGradient>
    </defs>
    <polygon points="664,0 1066,0 1066,600 660,600 494,252" fill="url(#g-close)" role="img" aria-label="Photo: two smiling businessmen shaking hands"/>
    <polyline points="493,302 662,420 552,600" fill="none" stroke="#9fd6d3" stroke-width="1.2"/>
    <polygon points="576,600 710,418 1066,600" fill="var(--blue)"/>
  </svg>
  <div class="brand">KALDENA_OPS</div>
  <h2>Thank you</h2>
  <div class="mail"><svg width="26" height="20" viewBox="0 0 26 20" fill="none" stroke="#333" stroke-width="1.8"><rect x="1" y="1" width="24" height="18"/><path d="M1,1 L13,11 L25,1"/></svg>info@kaldena.example</div>
</section>

</body>
</html>
```